Quillbrook IT company focused on 3 areas of IT

Looking for something similar to attached cards. Logo for quillbrook also attached.. Looking for something clean as far as colors (surprise me).. Quill stands for 3 primary areas, web design, consulting and network infrastructure design. Please email me if you have any questions. Looking forward to seeing how creative and professional this card will look. Thank you,

Target Market(s)

Small business/consumers looking for It services

Industry/Entity Type

It Service

Contact Information for Business Card

Dorin Vasek
Principal Consultant

202-555-0173

www.quillbrook-example.com
dvasek@quillbrook-example.com

27416 Copper Lantern Way,
Germantown, MD 20999

Colors

Designer to choose colors to be used in the design.

Requirements
Must have
• attached Logo design. Feel free to play with the colors.. If you have a better idea for a card, please fee free to send me. Looking for something clean/modern. Should have tech feel, not cheesy.
Nice to have
• Surprise me :-)..

```html
<!DOCTYPE html>
<html lang="en">
<head>
<meta charset="utf-8">
<title>Quillbrook Business Card</title>
<link rel="stylesheet" href="https://fonts.googleapis.com/css2?family=Lato:wght@300;400;700;900&display=swap">
<style>
  :root {
    --stage: #e4e4e4;
    --ink: #1e1e1e;
    --ink-soft: #2a2a2a;
    --paper: #ffffff;
    --logo-ink: #1f2a2c;
  }
  * { box-sizing: border-box; margin: 0; padding: 0; }
  html, body {
    width: 1200px; height: 900px; overflow: hidden;
    background: var(--stage);
    font-family: "Lato", Arial, sans-serif;
  }
  .stage { position: relative; width: 1200px; height: 900px; }

  /* Back of card */
  .card-back {
    position: absolute; left: 90px; top: 290px;
    width: 560px; height: 320px;
    background: var(--ink-soft);
    border-radius: 16px;
    color: var(--paper);
    display: flex; flex-direction: column; align-items: center; justify-content: center;
    box-shadow: 0 10px 26px rgba(0,0,0,.18);
  }
  .brand { display: flex; align-items: center; gap: 12px; }
  .brand-square { width: 20px; height: 20px; background: currentColor; }
  .brand-name { font-weight: 900; font-size: 40px; letter-spacing: 2px; text-transform: uppercase; }
  .card-back .website {
    position: absolute; bottom: 36px;
    font-size: 13px; font-weight: 700; letter-spacing: 2.5px;
  }

  /* Front of card */
  .card-front {
    position: absolute; left: 770px; top: 170px;
    width: 320px; height: 560px;
    background: var(--paper);
    border-radius: 16px;
    overflow: hidden;
    box-shadow: 0 10px 26px rgba(0,0,0,.18);
  }
  .logo-area {
    height: 200px; display: flex; align-items: center; justify-content: center;
    color: var(--logo-ink);
  }
  .logo-area .brand-name { font-size: 30px; }
  .logo-area .brand-square { width: 16px; height: 16px; }

  .name-band {
    height: 104px; background: var(--ink); color: var(--paper);
    padding: 22px 28px 0 56px;
  }
  .person { font-size: 27px; text-transform: uppercase; letter-spacing: 1px; }
  .person .first { font-weight: 900; }
  .person .last { font-weight: 300; }
  .role { font-size: 19px; font-weight: 400; margin-top: 4px; }

  .contacts { padding: 14px 16px 0 16px; display: flex; flex-direction: column; gap: 8px; }
  .contact-row { display: flex; gap: 8px; }
  .contact-icon {
    width: 52px; flex: none; background: var(--ink);
    display: flex; align-items: flex-start; justify-content: center; padding-top: 12px;
  }
  .contact-icon svg { width: 26px; height: 26px; }
  .contact-text {
    flex: 1; background: var(--ink); color: var(--paper);
    font-size: 14px; font-weight: 400; line-height: 1.35;
    padding: 16px 10px; min-height: 52px;
  }
  .contact-text.phone { font-size: 19px; padding-top: 13px; }
</style>
</head>
<body>
<main class="stage">

  <section class="card-back" aria-label="Card back">
    <div class="brand">
      <span class="brand-square"></span>
      <span class="brand-name">Quillbrook</span>
    </div>
    <p class="website">www.quillbrook-example.com</p>
  </section>

  <section class="card-front" aria-label="Card front">
    <div class="logo-area">
      <div class="brand">
        <span class="brand-square"></span>
        <span class="brand-name">Quillbrook</span>
      </div>
    </div>

    <div class="name-band">
      <p class="person"><span class="first">Dorin</span> <span class="last">Vasek</span></p>
      <p class="role">Principal Consultant</p>
    </div>

    <div class="contacts">
      <div class="contact-row">
        <div class="contact-icon">
          <svg viewBox="0 0 24 24" fill="#fff" aria-hidden="true">
            <path d="M6.6 10.8a15.1 15.1 0 0 0 6.6 6.6l2.2-2.2a1 1 0 0 1 1-.25 11.4 11.4 0 0 0 3.6.57 1 1 0 0 1 1 1V20a1 1 0 0 1-1 1A17 17 0 0 1 3 4a1 1 0 0 1 1-1h3.5a1 1 0 0 1 1 1c0 1.25.2 2.450.57 3.57a1 1 0 0 1-.25 1z"/>
          </svg>
        </div>
        <p class="contact-text phone">202-555-0173</p>
      </div>

      <div class="contact-row">
        <div class="contact-icon">
          <svg viewBox="0 0 24 24" fill="none" stroke="#fff" stroke-width="1.6" aria-hidden="true">
            <rect x="3" y="6" width="18" height="12"/>
            <path d="M3 6l9 7 9-7M3 18l7-6M21 18l-7-6"/>
          </svg>
        </div>
        <p class="contact-text">dvasek@quillbrook-example.com</p>
      </div>

      <div class="contact-row">
        <div class="contact-icon">
          <svg viewBox="0 0 24 24" fill="#fff" aria-hidden="true">
            <path d="M12 2a7 7 0 0 0-7 7c0 5 7 13 7 13s7-8 7-13a7 7 0 0 0-7-7zm0 9.5A2.5 2.5 0 1 1 12 6.5a2.5 2.5 0 0 1 0 5z"/>
          </svg>
        </div>
        <p class="contact-text">27416 Copper Lantern Way,<br>Larkmoor, OR 20999</p>
      </div>
    </div>
  </section>

</main>
</body>
</html>
```